Website for Barlow Fabrication & Building Ltd

General Note to all.

1. Piling and gas works are separate areas of work and should not be put together.
- the marine section should really be the piling works and should have all the barges/water piles etc.
- the gas section should have the big silo looking thing

2. I would like to add in Specialist Onsite Labour and Management in the 'our services' section. The would include the Supervisors, Coded Welders, Site Fitters and Crane and Rig Crews etc.

3. I did like it how someone had use the BFB header logo as the top of the webpage with the individual tabs above and the website starting below. Please remove the VAT number and phone number from this section.

4. I also liked how one designer incorporate the orange line with spark (from the logo) as a page separator representing the welding part of the business

5. Add in a Mission Statement - To go above and beyond in to ensure our clients projects are delivered safely, ahead of schedule, in any environment for the benefit of not only our customers but also our employees and communities we work in.

6. Add in Business Objectives -BFB is on a mission to be one of the leading contractors in UK to supply All Site Labour - ranging from Site Management, fully Coded Welders, Site Fitters and Crane and Rig Crews.

7. I am happy for you to add in photos that are not ours for the thumbs nails for the our services. ie a colourful welding pics/cool tunnelling pic etc - just make sure I will not get done for copy write infringements

8. I would like a some type of 'contact us' field or 'request a consultation' section.

9. Please confirm if the webpages you create will be compatible for both desktop and mobile app and how difficult it will be to update personally once it is live.

10. You have all done very well and have thus far been very impressed with what you have produced. I gave a very vague brief as I was not entirely sure how you would go about making something with very little information. Some of the designs look very professional.

11. I'm not sure how once I choose the winning design how that then transfers over to my domain? Perhaps someone can help me with that? I will also be looking for a web hosting platform so feel free to provide this information.

After using Sketch hive for successful getting a professional logo for the company I'm giving the web design option a go.

I am looking for a professional website for the above civil construction company.

The company director has many years experience in Marine, tunnelling, conveyors, stadium construction gas and piling works including piling works for coal ports, bridges and tunnels.

The company currently provide 20+ skilled and experienced guys from all trades (supervisors, coded welders, fitters, crane drivers and crane supervisors, rigglers, slingers and piling operatives) on the Corran Shoreline project in London - London's new super sewer. Most of this work is off barges carrying cranes (upto 600T and drill rigs).

As we are looking to expand and get more subcontracts we need a web presence to say who we are and what we do.

I'll include the 2 company logos we currently use below

I have included an info doc with pics you may or may not use.

Target Market(s)

Mainly other large construction companies and potential subcontractors

Industry/Entity Type

Construction Company

Coding

Coded - Design and coding required

Font styles to use
Sans Serif

Colors
0655a3
f37122
ffffff

Requirements
Must have
• Few tabs
• Simple to use/update but still professional look
• The challenge will be making the website look professional with not much available content.
Should not have
• No residential house building

```html
<!DOCTYPE html>
<html lang="en">
<head>
<meta charset="utf-8">
<title>Barlow Fabrication &amp; Building Ltd</title>
<link href="https://fonts.googleapis.com/css2?family=Open+Sans:wght@400;600;700&family=Roboto:wght@400;500;700&display=swap" rel="stylesheet">
<style>
:root{
  --blue:#0655a3;
  --blue-dark:#0a4a8f;
  --orange:#f37122;
  --white:#ffffff;
  --ink:#222a33;
  --muted:#7b838c;
  --pale:#eef2f8;
  --line:#e2e6ec;
  --grey-band:#f3f4f6;
}
*{box-sizing:border-box;margin:0;padding:0}
html,body{width:1200px;height:4054px;overflow:hidden}
body{font-family:"Open Sans",Arial,sans-serif;color:var(--ink);background:var(--white);position:relative}
h1,h2,h3,h4{font-family:"Roboto",Arial,sans-serif}
.section{position:absolute;left:0;width:1200px}
.section-title{position:absolute;left:0;width:1200px;text-align:center;color:var(--blue);font-size:27px;font-weight:700;letter-spacing:.5px}
.btn-outline{display:inline-block;border:2px solid var(--orange);color:var(--orange);font:600 13px "Roboto",sans-serif;padding:9px 18px;text-transform:uppercase;letter-spacing:.5px}
.btn-outline.light{border-color:var(--white);color:var(--white)}
/* header */
.site-header{top:0;height:115px;background:var(--white);box-shadow:0 2px 6px rgba(0,0,0,.06);z-index:2}
.brand{position:absolute;left:98px;top:12px;display:flex;align-items:center;gap:10px}
.brand-mark{width:16px;height:16px;border-radius:50%;background:var(--orange)}
.brand-name{font:700 34px "Roboto",sans-serif;color:var(--blue);letter-spacing:1px}
.quote-btn{position:absolute;right:100px;top:18px;background:var(--orange);color:var(--white);font:600 15px "Roboto",sans-serif;padding:13px 20px;text-transform:uppercase}
.main-nav{position:absolute;right:100px;top:76px;display:flex;gap:28px;font:500 16px "Roboto",sans-serif;color:#555}
.main-nav .active{color:var(--blue)}
.search-icon{margin-left:4px}
/* hero */
.hero{top:115px;height:477px;background:linear-gradient(180deg,#6c86a8 0%,#4c6587 45%,#1e3450 100%)}
.hero-title{position:absolute;top:110px;width:1200px;text-align:center;color:var(--white);font:700 48px "Roboto",sans-serif;letter-spacing:1px}
.hero-sub{position:absolute;top:176px;left:230px;width:740px;text-align:center;color:var(--white);font:700 24px/1.4 "Open Sans",sans-serif}
.hero-btn{position:absolute;top:260px;left:518px;background:var(--orange);color:var(--white);font:600 17px "Roboto",sans-serif;padding:15px 22px;text-transform:uppercase}
.dots{position:absolute;top:430px;left:574px;display:flex;gap:6px}
.dots span{width:10px;height:10px;border-radius:50%;border:1.5px solid var(--white)}
.dots span.on{background:var(--white)}
/* why */
.why{top:592px;height:568px;background:var(--white)}
.why .section-title{top:88px}
.why-intro{position:absolute;top:136px;left:225px;width:750px;text-align:center;font-size:13px;line-height:1.6;color:var(--muted)}
.cards{position:absolute;top:218px;left:100px;width:1000px;display:flex;gap:16px}
.card{flex:1;height:240px;border:1px solid var(--line);text-align:center;padding-top:40px;position:relative;background:var(--white)}
.card h3{font-size:16px;font-weight:700;margin-bottom:18px}
.card p{font-size:12.5px;line-height:1.65;color:var(--muted);width:230px;margin:0 auto 18px}
.card.featured{background:var(--orange);border-color:var(--orange);color:var(--white)}
.card.featured p{color:var(--white)}
.card-icon{position:absolute;top:-28px;left:50%;margin-left:-28px;width:56px;height:56px;border-radius:50%;background:var(--white);display:flex;align-items:center;justify-content:center}
/* about */
.about{top:1160px;height:495px;background:var(--pale)}
.about-photo{position:absolute;left:0;top:0;width:600px;height:495px;background:linear-gradient(120deg,#c9d4e2 0%,#e6ebf2 55%,#d7c88a 70%,#e9edf3 100%)}
.about-body{position:absolute;left:603px;top:92px;width:497px}
.about-body h2{color:var(--blue);font-size:27px;font-weight:700;margin-bottom:18px}
.about-body p{font-size:12px;line-height:1.95;color:var(--muted);margin-bottom:20px}
/* projects */
.projects{top:1655px;height:817px;background:var(--white)}
.projects .section-title{top:110px}
.grid{position:absolute;top:183px;left:100px;width:1000px;display:grid;grid-template-columns:repeat(3,318px);grid-gap:23px 23px}
.tile{height:253px}
.tile.intro{background:var(--blue);color:var(--white);text-align:center;padding-top:56px}
.tile.intro h3{font-size:21px;margin-bottom:12px}
.tile.intro p{font-size:13px;line-height:1.5;margin:0 auto 18px;width:220px}
.t1{background:linear-gradient(180deg,#cfd8e0,#8a6b5e 60%,#3f3d3c)}
.t2{background:linear-gradient(180deg,#c7d3dd,#5a5e63 60%,#2c2e31)}
.t3{background:linear-gradient(180deg,#b5c2c9,#7c8576 55%,#5b5a4f)}
.t4{background:linear-gradient(180deg,#6f9ecc,#a5c1db 55%,#2d3440)}
.t5{background:linear-gradient(180deg,#d2dbe6,#8a8f7c 55%,#5b5a4a)}
/* experience */
.experience{top:2472px;height:501px;background:var(--pale)}
.experience h2{position:absolute;left:100px;top:86px;color:var(--blue);font-size:27px;font-weight:700}
.exp-list{position:absolute;left:100px;top:152px;width:740px;display:grid;grid-template-columns:370px 370px;row-gap:32px}
.exp-item{display:flex;gap:14px}
.exp-icon{flex:0 0 80px;width:80px;height:80px;border-radius:50%;border:2px solid #e9b28f;display:flex;align-items:center;justify-content:center;background:var(--white)}
.exp-icon.on{background:var(--orange);border-color:var(--orange)}
.exp-item h4{font-size:16px;font-weight:700;margin:6px 0 10px}
.exp-item p{font-size:11.5px;line-height:1.7;color:var(--muted);width:220px}
.exp-person{position:absolute;left:855px;top:30px;width:280px;height:471px;background:linear-gradient(180deg,var(--pale) 0%,#c8d5e6 40%,#6f8fb8 100%);border-radius:140px 140px 0 0}
/* testimonials */
.clients{top:2973px;height:457px;background:var(--white)}
.clients .section-title{top:92px}
.quotes{position:absolute;top:155px;left:100px;width:1000px;display:flex;gap:42px}
.quote{flex:1;height:197px;border:1px solid var(--line);padding:22px 28px}
.quote p{font-size:13px;line-height:1.7;color:var(--muted);margin-bottom:18px}
.quote p b{color:#cfc6c0;font:700 26px "Roboto",sans-serif;vertical-align:-6px;margin-right:6px}
.who{display:flex;align-items:center;gap:14px}
.avatar{width:58px;height:58px;border-radius:50%;background:linear-gradient(135deg,#c9a994,#8b6f63)}
.who h4{font:600 14px "Open Sans",sans-serif}
.who span{font-size:11px;color:var(--muted)}
.stars{margin-left:auto;color:var(--orange);font-size:20px;letter-spacing:2px}
.arrow{position:absolute;top:235px;font-size:22px;color:#999}
/* partners */
.partners{top:3430px;height:255px;background:var(--grey-band)}
.partner-row{position:absolute;top:80px;left:100px;width:1000px;display:flex;gap:40px}
.partner{width:218px;height:120px;background:var(--white);border:1px solid var(--line);display:flex;align-items:center;justify-content:center;gap:8px;font:700 17px "Roboto",sans-serif;color:var(--blue)}
.partner.raised{box-shadow:0 3px 10px rgba(0,0,0,.15)}
.p-sq{width:12px;height:12px;background:var(--blue)}
.p-ci{width:12px;height:12px;border-radius:50%;background:var(--blue)}
.nav-arrow{position:absolute;top:135px;width:46px;border-top:3px solid var(--blue);color:var(--blue)}
.nav-arrow span{position:absolute;top:-26px;font-size:20px}
/* footer */
.site-footer{top:3685px;height:369px;background:linear-gradient(180deg,var(--blue) 0%,var(--blue-dark) 100%);color:var(--white)}
.foot-nav{position:absolute;top:50px;left:100px;width:1000px;display:flex;justify-content:space-between;font:500 16px "Roboto",sans-serif}
.foot-rule{position:absolute;top:118px;left:100px;width:1000px;border-top:1px solid rgba(255,255,255,.25)}
.foot-brand{position:absolute;top:178px;left:100px;display:flex;align-items:center;gap:10px;font:700 34px "Roboto",sans-serif}
.foot-brand i{width:16px;height:16px;border-radius:50%;background:var(--orange)}
.foot-text{position:absolute;top:176px;left:262px;width:620px;font-size:12px;line-height:1.9;color:#dbe6f3}
.social{position:absolute;top:200px;right:100px;display:flex;gap:24px}
.social span{width:16px;height:16px;border-radius:50%;border:2px solid var(--white)}
.copyright{position:absolute;top:330px;width:1200px;text-align:center;font-size:12px;color:#dbe6f3}
</style>
</head>
<body>

<header class="section site-header">
  <div class="brand"><span class="brand-mark"></span><span class="brand-name">BFB</span></div>
  <div class="quote-btn">Get a quote</div>
  <nav class="main-nav">
    <span class="active">Home</span><span>About</span><span>Our Projects</span><span>Services</span><span>Testimonials</span><span>Contact</span>
    <svg class="search-icon" width="16" height="16" viewBox="0 0 16 16"><circle cx="6.5" cy="6.5" r="5" fill="none" stroke="#555" stroke-width="2"/><line x1="10.5" y1="10.5" x2="15" y2="15" stroke="#555" stroke-width="2"/></svg>
  </nav>
</header>

<section class="section hero" role="img" aria-label="Harbour construction site with cranes and barges at dusk">
  <h1 class="hero-title">BARLOW FABRICATION &amp; BUILDING</h1>
  <p class="hero-sub">Barlow Fabrication &amp; Building has over 15 years experience working in the civil construction industry</p>
  <div class="hero-btn">View projects</div>
  <div class="dots"><span class="on"></span><span></span><span></span><span></span></div>
</section>

<section class="section why">
  <h2 class="section-title">WHY CHOOSE US</h2>
  <p class="why-intro">Sed ut perspiciatis unde omnis iste natus error sit voluptatem accusantium doloremque laudantium, totamam rem aperiam, eaq ue ipsa quae ab illo inventore veritatie explicabo voluptas sit</p>
  <div class="cards">
    <div class="card"><h3>PROFESSIONAL TEAM</h3><p>Lorem Ipsum is simply dummy text. Lorem Ipsum is simply dummy text of the printing and typesetting industry.</p><span class="btn-outline">Read more</span></div>
    <div class="card featured">
      <div class="card-icon"><svg width="24" height="24" viewBox="0 0 24 24"><path d="M6.6 10.8a15 15 0 0 0 6.6 6.6l2.2-2.2a1 1 0 0 1 1-.25 11.4 11.4 0 0 0 3.6.57 1 1 0 0 1 1 1V20a1 1 0 0 1-1 1A17 17 0 0 1 3 4a1 1 0 0 1 1-1h3.5a1 1 0 0 1 1 1c0 1.25.2 2.45.57 3.57a1 1 0 0 1-.25 1z" fill="#f37122"/></svg></div>
      <h3>24 / 7 SUPPORT</h3><p>Lorem Ipsum is simply dummy text. Lorem Ipsum is simply dummy text of the printing and typesetting industry.</p><span class="btn-outline light">Read more</span></div>
    <div class="card"><h3>AFFORDABLE PRICE</h3><p>Lorem Ipsum is simply dummy text. Lorem Ipsum is simply dummy text of the printing and typesetting industry.</p><span class="btn-outline">Read more</span></div>
  </div>
</section>

<section class="section about">
  <div class="about-photo" role="img" aria-label="Yellow safety helmet resting on construction drawings and tools"></div>
  <div class="about-body">
    <h2>ABOUT THE COMPANY DIRECTOR</h2>
    <p>Daniel Barlow was born and raised in South East London. After finishing school he completed a Welding and Fabrication apprenticeship with Kestrel Welders and Harrowgate Civil. During this time he gained a lot of experience in structural steel welding becoming a coded welder and working on both the Riverside and Northgate stadiums. Soon after completing his apprenticeship he moved over to Australia and was fortunate to work for some of the most prestigious civil construction companies: Fenwick Marsh, Carrick Industrial and Stonecroft. Here he was also able to gain additional qualifications in Rigging and Open Crane Operating making him an exceptional all-rounder on site.</p>
    <span class="btn-outline">Read more</span>
  </div>
</section>

<section class="section projects">
  <h2 class="section-title">RECENT PROJECTS</h2>
  <div class="grid">
    <div class="tile intro"><h3>Sed ut perspiciatis</h3><p>Lorem ipsum dolor sit amet, consectetuer adipiscing elit, sed tincidunt ut</p><span class="btn-outline light">Read more</span></div>
    <div class="tile t1" role="img" aria-label="Red crawler crane on a river barge"></div>
    <div class="tile t2" role="img" aria-label="Steel piling rig beside the river"></div>
    <div class="tile t3" role="img" aria-label="Work barges moored on the river"></div>
    <div class="tile t4" role="img" aria-label="Cranes above a bridge structure against blue sky"></div>
    <div class="tile t5" role="img" aria-label="Piling barge alongside a riverside wall"></div>
  </div>
</section>

<section class="section experience">
  <h2>OUR EXPERIENCE</h2>
  <div class="exp-list">
    <div class="exp-item"><div class="exp-icon on"><svg width="34" height="34" viewBox="0 0 34 34"><path d="M17 4v22M9 12h16M6 20c2 6 7 8 11 8s9-2 11-8" fill="none" stroke="#fff" stroke-width="2.5"/><circle cx="17" cy="5" r="2.5" fill="none" stroke="#fff" stroke-width="2"/></svg></div><div><h4>Marine</h4><p>Lorem Ipsum is simply dummy text for a the printing . It is Lorem Ipsum has been thare industry's standard dummy.</p></div></div>
    <div class="exp-item"><div class="exp-icon"><svg width="34" height="34" viewBox="0 0 34 34"><path d="M5 28V16a12 12 0 0 1 24 0v12M11 28V17a6 6 0 0 1 12 0v11" fill="none" stroke="#f37122" stroke-width="2.5"/></svg></div><div><h4>Tunnelling</h4><p>Lorem Ipsum is simply dummy text for a the printing . It is Lorem Ipsum has been thare industry's standard dummy.</p></div></div>
    <div class="exp-item"><div class="exp-icon"><svg width="34" height="34" viewBox="0 0 34 34"><rect x="4" y="14" width="26" height="8" rx="4" fill="none" stroke="#f37122" stroke-width="2.5"/><rect x="10" y="7" width="6" height="6" fill="none" stroke="#f37122" stroke-width="2"/><path d="M8 22v7M26 22v7" stroke="#f37122" stroke-width="2.5"/></svg></div><div><h4>Conveyors</h4><p>Lorem Ipsum is simply dummy text for a the printing . It is Lorem Ipsum has been thare industry's standard dummy.</p></div></div>
    <div class="exp-item"><div class="exp-icon"><svg width="34" height="34" viewBox="0 0 34 34"><path d="M8 29V6h4v23M6 6h20l-8 8M22 14v15" fill="none" stroke="#f37122" stroke-width="2.5"/></svg></div><div><h4>Piling Works</h4><p>Lorem Ipsum is simply dummy text for a the printing . It is Lorem Ipsum has been thare industry's standard dummy.</p></div></div>
  </div>
  <div class="exp-person" role="img" aria-label="Site engineer in a blue hard hat holding rolled plans"></div>
</section>

<section class="section clients">
  <h2 class="section-title">WORDS FROM CLIENTS</h2>
  <span class="arrow" style="left:44px">&#8249;</span>
  <span class="arrow" style="right:44px">&#8250;</span>
  <div class="quotes">
    <div class="quote"><p><b>&ldquo;</b>Sed quia consequuntur magni dolores eos qui ratione volup tatem sequi nesciunt. Neque porro quisquam est, qui dolorem ipsum quia dolor sit amet.</p>
      <div class="who"><div class="avatar" role="img" aria-label="Client portrait"></div><div><h4>John Deo</h4><span>London</span></div><div class="stars">&#9733;&#9733;&#9733;&#9733;&#9733;</div></div></div>
    <div class="quote"><p><b>&ldquo;</b>Sed quia consequuntur magni dolores eos qui ratione volup tatem sequi nesciunt. Neque porro quisquam est, qui dolorem ipsum quia dolor sit amet.</p>
      <div class="who"><div class="avatar" role="img" aria-label="Client portrait"></div><div><h4>Jenifer Steffy</h4><span>London</span></div><div class="stars">&#9733;&#9733;&#9733;&#9733;&#9733;</div></div></div>
  </div>
</section>

<section class="section partners">
  <div class="nav-arrow" style="left:42px"><span style="left:4px">&#8249;</span></div>
  <div class="nav-arrow" style="right:42px"><span style="right:4px">&#8250;</span></div>
  <div class="partner-row">
    <div class="partner raised"><i class="p-sq"></i>Corran Shoreline</div>
    <div class="partner">Fenwick Marsh</div>
    <div class="partner"><i class="p-ci"></i>Harrowgate Civil</div>
    <div class="partner">Deepbore</div>
  </div>
</section>

<footer class="section site-footer">
  <nav class="foot-nav"><span>Home</span><span>About</span><span>Our Projects</span><span>Services</span><span>Testimonials</span><span>Contact</span></nav>
  <div class="foot-rule"></div>
  <div class="foot-brand"><i></i>BFB</div>
  <p class="foot-text">Sed ut perspiciatis unde omnis iste natus error sit voluptatem accusantium dolo remque laudantium, totam rem aperiam, eaque ipsa quae ab illo inventore veritatis et quasi architecto beatae vitae dicta sunt explicabo. Nemo enim ipsam voluptatem quia voluptas aspernatur aut odit aut fugit consequntur magni</p>
  <div class="social" aria-label="Social links"><span></span><span></span><span></span></div>
  <p class="copyright">Copyright &copy; 2018. All rights reserved</p>
</footer>

</body>
</html>
```